Business Card: RW Office Partners - Your organised problem solver

Business Name: RW Office Partners
Website: www.rwofficepartners.com.au
Email: marisol@rwofficepartners.com.au
Mobile: 61 482 907 236
Facebook: @rwofficepartners
Instrgram: @rwofficepartners

Brading Colours:
HEX
#986474
#ddccd3
#7a8498
#c9d8e4
#000000
#ffffff

Tag Line: Your organised problem solver

Link to DRAFT website:
https://deskhelpcollective.wixsite.com/rw-office-partners

About Page from the website:
My name is Marisol Wrenfield, and I would love to assist you to become more productive in your day to day and achieve your business and personal goals.
My mission is to give you time, time to work on the important tasks of your business or to be able to spend more time with your family. I will take on the tasks you don’t have time for, don’t know well or simply don’t like to do.
I have an extensive background in Administration, Tender Coordination, Document Control, WHS and Quality Management working primarily in the Construction, Mining and Corporate World.
I am passionate about being organised, having order and making things in your life (and mine) easier! I love to watch something unfold and grow into something amazing! I am known for being the go-to problem solver, the organiser of all things, producing high standards of work even under pressure. I’m also a confident communicator, and I understand that you’re busy running your business.

Target Market(s)

Small to Medium Business who require assistance in their business by a virtual assistant.

Industry/Entity Type

Virtual Assistant

Contact Information for Business Card

Mobile: 61 482 907 236

Font styles to use
Sans Serif

Colors
ffffff

Requirements
Must have
• Branding Colours as outlined.
Contact Details as outlined.
Logo as provided.
Proper contact details - mobile, facebook, instragm, website.
Simple, Elegant, very clean looking.
Should not have
• Note cute with pictures.
Not too girly as still want to market to construction companies.

```html
<!DOCTYPE html>
<html lang="en">
<head>
<meta charset="utf-8">
<title>RW Office Partners – Business Card</title>
<link rel="stylesheet" href="https://fonts.googleapis.com/css2?family=Roboto:wght@400;500&family=Fira+Sans:wght@500&family=Montserrat:wght@500&display=swap">
<style>
  :root {
    --plum: #986474;
    --plum-soft: #ddccd3;
    --slate: #7a8498;
    --slate-soft: #c9d8e4;
    --ink: #2b2b2b;
    --paper: #ffffff;
    --backdrop: #e9e7e8;
    --muted: #8d8d90;
  }
  * { box-sizing: border-box; margin: 0; padding: 0; }
  html, body { width: 1200px; height: 1200px; overflow: hidden; }
  body {
    background: var(--backdrop);
    font-family: "Roboto", Arial, sans-serif;
    position: relative;
  }
  .card {
    position: absolute;
    left: 244px;
    width: 712px;
    height: 416px;
    background: var(--paper);
    border-radius: 26px;
    overflow: hidden;
    box-shadow: 0 10px 28px rgba(0,0,0,0.12);
  }
  .card--front { top: 120px; }
  .card--back { top: 645px; }

  .brand-name {
    position: absolute;
    left: 0; right: 0;
    text-align: center;
    font-family: "Montserrat", Arial, sans-serif;
    font-weight: 500;
    color: var(--slate);
    text-transform: uppercase;
    letter-spacing: 1px;
    white-space: nowrap;
  }
  .card--front .brand-name { top: 150px; font-size: 50px; }
  .card--back .brand-name { top: 70px; font-size: 46px; }

  .socials {
    position: absolute;
    left: 0; right: 0;
    display: flex;
    justify-content: center;
    gap: 18px;
    font-size: 18px;
    color: var(--ink);
  }
  .card--front .socials { top: 350px; }
  .card--back .socials { top: 370px; }
  .social { display: flex; align-items: center; gap: 9px; }
  .social-mark {
    width: 15px; height: 15px;
    border-radius: 3px;
    background: var(--plum);
  }

  .split-band {
    position: absolute;
    left: 0; right: 0; bottom: 0;
    height: 16px;
    display: flex;
  }
  .split-band span { flex: 1; }
  .split-band .band-plum { background: var(--plum); }
  .split-band .band-slate { background: var(--slate); }

  .person {
    position: absolute;
    right: 431px;
    top: 220px;
    text-align: right;
  }
  .person-name {
    font-family: "Fira Sans", Arial, sans-serif;
    font-weight: 500;
    font-size: 27px;
    color: var(--plum);
    white-space: nowrap;
  }
  .person-role {
    font-size: 18px;
    color: var(--ink);
    margin-top: 4px;
  }
  .divider {
    position: absolute;
    left: 303px;
    top: 208px;
    width: 1.5px;
    height: 80px;
    background: #9a9a9e;
  }
  .contacts {
    position: absolute;
    left: 328px;
    top: 208px;
    list-style: none;
    font-size: 19px;
    color: var(--ink);
  }
  .contacts li {
    display: flex;
    align-items: center;
    gap: 12px;
    height: 26px;
  }
  .contacts svg { width: 18px; height: 18px; fill: var(--plum); flex: none; }

  .tagline-band {
    position: absolute;
    left: 0; right: 0;
    top: 313px;
    height: 34px;
    background: linear-gradient(90deg, var(--plum) 0%, var(--plum) 45%, var(--slate) 100%);
    color: var(--paper);
    font-family: "Montserrat", Arial, sans-serif;
    font-weight: 500;
    font-size: 17px;
    letter-spacing: 1.6px;
    word-spacing: 5px;
    display: flex;
    align-items: center;
    justify-content: center;
    text-transform: uppercase;
  }
</style>
</head>
<body>

<section class="card card--front">
  <div class="brand-name">RW Office Partners</div>
  <div class="socials">
    <span class="social"><span class="social-mark"></span>@rwofficepartners</span>
    <span class="social"><span class="social-mark"></span>@rwofficepartners</span>
  </div>
  <div class="split-band"><span class="band-plum"></span><span class="band-slate"></span></div>
</section>

<section class="card card--back">
  <div class="brand-name">RW Office Partners</div>

  <div class="person">
    <div class="person-name">Marisol Wrenfield</div>
    <div class="person-role">Virtual Assistant</div>
  </div>
  <div class="divider"></div>

  <ul class="contacts">
    <li>
      <svg viewBox="0 0 24 24" aria-hidden="true"><path d="M3 8c0-2 4-4 9-4s9 2 9 4v2h-5V8H8v2H3zM6 11h12l2 8H4z M12 13a2.5 2.5 0 1 0 0.01 0z"/></svg>
      61 482 907 236
    </li>
    <li>
      <svg viewBox="0 0 24 24" aria-hidden="true"><path d="M2 5h20v14H2z M3 6l9 7 9-7" stroke="#fff" stroke-width="1.5"/></svg>
      marisol@rwofficepartners.com.au
    </li>
    <li>
      <svg viewBox="0 0 24 24" aria-hidden="true"><circle cx="12" cy="12" r="10"/><path d="M2 12h20M12 2c-4 5-4 15 0 20M12 2c4 5 4 15 0 20M4 7h16M4 17h16" stroke="#fff" stroke-width="1.2" fill="none"/></svg>
      www.rwofficepartners.com.au
    </li>
  </ul>

  <div class="tagline-band">Your organised problem solver</div>

  <div class="socials">
    <span class="social"><span class="social-mark"></span>@rwofficepartners</span>
    <span class="social"><span class="social-mark"></span>@rwofficepartners</span>
  </div>
</section>

</body>
</html>
```